Website development company website

ABOUT COMPANY
Hi everyone! We're a Melbourne, Australia website development company in a need of a website design that will make online store merchants want to engage our services.
We specialise exclusively in Torvista e-commerce platform (https://torvista-platform.example/). What distinguishes our business from competition is that rather than designing and building brand new websites, we offer development, support and maintenance services to established websites. Maintenance and Support are the keywords representing our business.
Our potential clients are people with broken, slow and underperforming Torvista installations who need assistance getting their websites up and making sales. Our website must pass the message that we can help, and provide quick means of making contact.
DESIGN
Overall, we're looking for a slick, clean, airy, conservative design. No need to do anything crazy, try to stick to what's "standard" in website design these days and make it easy on all of us. The website is unlikely to be updated too often so it needs to look attractive and fresh first time over and after a year, too.
Attached is our new logo, which you'll be able to take the basic idea from, the colors and fonts. Though, don't use the fonts from the logo in the website, stick to the standard widely supported fonts. Additional use of Google fonts is fine.
Don't overdo it with colors, stick to conservative basic color set and only use the colors from the log for accents like headings etc. Please, don't be tempted to use the blue and orange as background of whole blocks, other than perhaps footer. Thanks.
For the images used, I'd like to stay away from a design studio/digital agency feel and lean more towards professional support and maintenance services. I'm thinking images of content merchants doing their job. Something along the lines of "We'll be taking care of the website so that you only need to care about the business".
Some ideas I like:
http://www.plumframe-pics.example/detail/photo/portrait-of-confident-male-design-professional-royalty-free-image/572048163
http://www.plumframe-pics.example/detail/photo/designer-taking-picture-of-hat-high-res-stock-photography/839207514
http://www.plumframe-pics.example/detail/photo/woman-packaging-pottery-royalty-free-image/216684093
Images of colorful shopping bags and shopping carts are over the top and not serious enough. Instead of images matching Online Shopping, I'd try going more for Stability, Reliability, Performance.
Our existing website is http://www.bravuln.example. Please, don't take design ideas from it, but it will give you a picture of the structure of our new website and content that's going to be used initially.
If you could include a basic icon set to use throughout the website, that would be great. If the icons could match our logo (attached), it would be a big plus.
ALL PAGES
Every page must contain clearly visible phone number (1300 648 907) and a Contact Us Now button, which opens an AJAX driven popup form with Name, Email, Phone and Message to be sent through.
To start with, main menu items will be Torvista, Portfolio, Contact.
At the bottom of each page, please, include a newsletter subscription form with text Subscribe to Torvista Support and Security Updates.
For the footer, I'd like to see a logo strip with the following logos in grayscale (no need to link anywhere): Torvista, QRX, DataVane, NCB. You'll find the logos on Google Images.
Standard footer columns follow. Here, I'd like to see logos in color: Torvista Certified Developer, Torvista Ceritified Solution Provider. Again, the logos are on Google Images.
No social media logos/links necessary anywhere on the website.
...and then the copyright line.
FRONT PAGE
Large slider with images that would appeal to our target audience. Keywords here would be Torvista System Audit, Torvista Performance Optimisation, Torvista Website Emergency Recovery, Torvista Development Infrastructure Hosting. We'll have a static page created for each of these to link to.
In a corner of the slider, or on the edge, can I have an overlay with logos in color (same as footer): Torvista Certified Developer, Torvista Ceritified Solution Provider.
Underneath, a number of blocks, each with an image and teaser that we'll use to link to various pages throughout the website.
PORTFOLIO PAGE
I'm thinking a single long page with a block per client, which will contain project name, description from us and a testimonial from client. Also, each block will contain a single large screenshot. No gallery or slideshow is necessary here, just one image per project.
I'll leave the layout up to you, but try to put yourself in the shoes of a potential client reviewing our past work by simply scrolling down this one page.
CONTACT US PAGE
Separate page with the same form as above, phone number (1300 648 907), email address (support@kavreo.example), address (Suite 42, Level 3|8 Wattlebrook Lane|Fernvale Heights VIC 3999), and a grayscale Plotway Map.
CODING UP
Coding up into static HTML/CSS/JS is equally important as the design itself. We're a website development company, we'll be integrating the theme. We will spot any issues and we will point them out.
Coded up design must be fully responsive. Enough said.
To be able to create any content in future, we'd like one extra page coded up with samples of all themed elements, lists, forms, buttons, 2, 3, 4-column layout, alerts, icons, etc. This page does not need to be designed, only coded up.
The design will be integrated into Drupal using Twig. If possible at all, try to keep it in mind when designing and coding up, and make the integration into a Drupal theme easier for us.
GOOD LUCK!
That's it. Let me know if anything needs clarifying. So far I've had a great experience with ArtFlockly. I don't doubt some great designs will emerge. Clever ideas are highly appreciated, but also make it clear you've read and followed the points in this brief. Cheers, Tom

```html
<!DOCTYPE html>
<html lang="en">
<head>
<meta charset="utf-8">
<title>Kavreo E-commerce</title>
<link href="https://fonts.googleapis.com/css2?family=Open+Sans:wght@400;600;700;800&display=swap" rel="stylesheet">
<style>
:root{
  --orange:#f07f1b;
  --blue:#1d4f86;
  --blue-dark:#163f6e;
  --navy-text:#24476d;
  --text:#333;
  --muted:#777;
  --light:#ececec;
  --portfolio-bg:#d8e0e8;
  --footer:#2c2c2c;
  --footer-bottom:#222;
  --white:#fff;
  --logo-grey:#a9a9a9;
}
*{box-sizing:border-box;margin:0;padding:0}
html,body{width:1200px;height:2970px;overflow:hidden}
body{font-family:"Open Sans",Arial,sans-serif;color:var(--text);background:var(--white);position:relative}
a{color:inherit;text-decoration:none}

/* header */
.site-header{position:absolute;top:0;left:0;width:1200px;height:88px;background:var(--white);border-top:4px solid var(--blue)}
.site-header::before{content:"";position:absolute;top:-4px;left:0;width:300px;height:4px;background:var(--orange)}
.brand{position:absolute;left:132px;top:24px;display:flex;align-items:center;gap:9px;white-space:nowrap}
.brand-mark{width:26px;height:34px;background:var(--blue);border-radius:3px}
.brand-name{font-size:21px;font-weight:800;color:var(--orange);letter-spacing:-.3px}
.main-nav{position:absolute;left:400px;top:0;height:84px;display:flex}
.main-nav a{display:block;padding:0 18px;line-height:84px;font-size:14px;color:#444;position:relative;white-space:nowrap}
.main-nav a.active{color:var(--navy-text);font-weight:600}
.main-nav a.active::after{content:"";position:absolute;left:18px;right:18px;bottom:16px;height:2px;background:var(--navy-text)}
.header-phone{position:absolute;left:900px;top:18px;height:50px;border-left:1px solid #ddd;width:170px;text-align:right;white-space:nowrap}
.header-phone small{display:block;font-size:13px;color:#555;line-height:18px}
.header-phone strong{display:block;font-size:23px;font-weight:600;color:var(--orange);line-height:28px}

/* hero */
.hero{position:absolute;top:88px;left:0;width:1200px;height:490px}
.hero-photo{position:absolute;inset:0;background:linear-gradient(110deg,#c9d4dd 0%,#8ea4b7 35%,#5d7892 60%,#aab9c6 100%)}
.hero-title{position:absolute;top:156px;left:0;width:1200px;text-align:center;font-size:0}
.hero-title span{display:inline-block;background:rgba(29,79,134,.78);color:var(--white);font-weight:800;font-size:31px;line-height:44px;letter-spacing:1px;padding:0 16px;margin-bottom:8px;text-transform:uppercase}
.hero-actions{position:absolute;top:282px;left:0;width:1200px;display:flex;justify-content:center;gap:20px}
.btn{display:inline-block;font-size:14px;text-align:center;line-height:34px;height:36px}
.btn-orange{background:var(--orange);color:var(--white);width:126px}
.btn-outline-light{border:2px solid var(--white);color:var(--white);width:126px;line-height:32px}
.hero-arrow{position:absolute;top:222px;width:52px;height:52px;background:rgba(255,255,255,.45);display:flex;align-items:center;justify-content:center}
.hero-arrow.prev{left:0}.hero-arrow.next{right:0}

/* tech strip */
.tech-strip{position:absolute;left:0;width:1200px;height:100px;display:flex;justify-content:center;align-items:center;gap:70px}
.tech-strip.top{top:578px;background:var(--light)}
.tech-strip.bottom{top:2486px;background:var(--white)}
.tech-strip span{font-size:30px;font-weight:700;color:var(--logo-grey);display:flex;align-items:center;gap:8px}
.tech-strip span i{display:inline-block;width:22px;height:22px;background:var(--logo-grey);border-radius:50%}

/* intro */
.intro{position:absolute;top:678px;left:0;width:1200px;height:482px;text-align:center}
.intro-kicker{position:absolute;top:32px;width:100%;font-size:13px;color:#444}
.intro-lead{position:absolute;top:62px;width:100%;font-size:25px;line-height:32px;color:#444;font-weight:400}
.intro-lead b{font-weight:600;color:#222}
.intro-cols{position:absolute;top:176px;left:132px;width:936px;display:flex}
.intro-col{width:468px;padding:0 60px}
.intro-col + .intro-col{border-left:1px solid #ddd}
.intro-col svg{display:block;margin:0 auto 18px}
.intro-col h3{font-size:17px;font-weight:600;color:#222;margin-bottom:16px}
.intro-col p{font-size:11.5px;line-height:20px;color:var(--muted)}

/* services */
.services{position:absolute;top:1160px;left:0;width:1200px;height:508px;background:linear-gradient(135deg,var(--blue) 0%,var(--blue-dark) 100%);text-align:center;color:var(--white)}
.section-title{font-size:25px;font-weight:400}
.section-title b{font-weight:600}
.services .section-title{position:absolute;top:34px;width:100%}
.services .section-sub{position:absolute;top:78px;width:100%;font-size:13px;color:#a9c1dc}
.service-cards{position:absolute;top:174px;left:132px;display:flex;gap:30px}
.service-card{width:292px;height:204px;background:var(--white);color:var(--text);position:relative;padding-top:66px;box-shadow:0 2px 6px rgba(0,0,0,.25)}
.service-icon{position:absolute;top:-34px;left:104px;width:84px;height:84px;border-radius:50%;display:flex;align-items:center;justify-content:center;border:4px solid var(--white)}
.service-card h3{font-size:17px;font-weight:600;color:#222}
.service-card p{font-size:11.5px;line-height:20px;color:var(--muted);padding:6px 26px 0}
.service-card .btn-grey{display:inline-block;margin-top:16px;background:#ececec;color:#aaa;font-size:11px;width:96px;line-height:26px}
.services-note{position:absolute;top:408px;width:100%;font-size:13px;color:#a9c1dc}
.btn-outline-white{position:absolute;top:444px;left:519px;width:162px;height:36px;border:2px solid var(--white);line-height:32px;font-size:14px;color:var(--white)}

/* testimonials */
.testimonials{position:absolute;top:1668px;left:0;width:1200px;height:310px}
.testimonials .section-title{position:absolute;top:32px;width:100%;text-align:center;color:#333}
.testimonials .section-sub{position:absolute;top:76px;width:100%;text-align:center;font-size:13px;color:#444}
.client-photo{position:absolute;top:150px;left:132px;width:112px;height:112px;border-radius:50%;background:linear-gradient(160deg,#cfd8e0,#6b7f93)}
.quote{position:absolute;top:146px;left:282px;width:790px;border-left:1px solid #e3e3e3;padding-left:34px}
.quote p{font-size:13.5px;line-height:26px;color:#555}
.quote cite{display:block;margin-top:14px;font-style:normal;font-size:14px;color:var(--orange);font-weight:600}
.quote cite span{color:#999;font-weight:400}

/* portfolio */
.portfolio{position:absolute;top:1978px;left:0;width:1200px;height:508px;background:var(--portfolio-bg)}
.portfolio .section-title{position:absolute;top:32px;width:100%;text-align:center;color:#333}
.portfolio .section-sub{position:absolute;top:76px;width:100%;text-align:center;font-size:13px;color:#444}
.project-list{position:absolute;top:136px;left:132px;display:flex;gap:30px}
.project{width:212px;background:var(--white);box-shadow:0 1px 3px rgba(0,0,0,.15)}
.project-shot{height:198px}
.project p{height:46px;line-height:46px;text-align:center;font-size:13.5px;color:#444}
.portfolio-arrow{position:absolute;top:228px}
.portfolio-arrow.prev{left:52px}.portfolio-arrow.next{right:52px}
.btn-outline-orange{position:absolute;top:442px;left:520px;width:160px;height:36px;border:2px solid var(--orange);line-height:32px;text-align:center;font-size:14px;color:var(--orange)}

/* footer */
.site-footer{position:absolute;top:2586px;left:0;width:1200px;height:326px;background:var(--footer);color:#ddd}
.footer-col{position:absolute;top:52px}
.footer-col h4{font-size:17px;font-weight:600;color:var(--orange);margin-bottom:28px}
.footer-links li{list-style:none;font-size:12.5px;line-height:27px}
.footer-col p{font-size:12.5px;line-height:22px}
.news-input{margin-top:18px;width:232px;height:34px;background:#444;display:flex;align-items:center;padding-left:12px;gap:10px;font-size:12px;color:#888}
.news-btn{margin-top:14px;width:110px;height:36px;background:var(--orange);color:var(--white);font-weight:700;font-size:14px;line-height:36px;text-align:center}
.footer-map{position:absolute;top:50px;left:794px;width:274px;height:156px;background:linear-gradient(135deg,#dfe6d5,#cfd9e3 60%,#e8e3d2)}
.map-link{position:absolute;top:216px;left:798px;font-size:12.5px;text-decoration:underline;color:#ddd}
.copyright{position:absolute;top:2912px;left:0;width:1200px;height:58px;background:var(--footer-bottom);color:#ddd;font-size:12.5px;line-height:58px;text-align:center}
.copyright em{font-style:normal;color:var(--orange)}
</style>
</head>
<body>

<header class="site-header">
  <a class="brand" href="#"><span class="brand-mark"></span><span class="brand-name">Kavreo E-commerce</span></a>
  <nav class="main-nav">
    <a class="active" href="#">Home</a>
    <a href="#">About Us</a>
    <a href="#">Torvista</a>
    <a href="#">Our Portfolio</a>
    <a href="#">Contact Us</a>
  </nav>
  <div class="header-phone"><small>Call Us Now!</small><strong>1300 648 907</strong></div>
</header>

<section class="hero">
  <div class="hero-photo" role="img" aria-label="Business team meeting in a bright office, smiling man in shirt and tie in front"></div>
  <h1 class="hero-title"><span>High performance Torvista sites</span><br><span>on time and on budget.</span></h1>
  <div class="hero-actions"><a class="btn btn-orange" href="#">Read More</a><a class="btn btn-outline-light" href="#">Contact Us</a></div>
  <a class="hero-arrow prev" href="#"><svg width="16" height="24"><path d="M12 3 3 12l9 9" stroke="#fff" stroke-width="2.5" fill="none"/></svg></a>
  <a class="hero-arrow next" href="#"><svg width="16" height="24"><path d="M4 3l9 9-9 9" stroke="#fff" stroke-width="2.5" fill="none"/></svg></a>
</section>

<div class="tech-strip top">
  <span>MarkSix</span><span><i></i>Torvista</span><span>Ferrite</span><span>QRX</span><span>NCB</span><span>DataVane</span>
</div>

<section class="intro">
  <p class="intro-kicker">Welcome to Kavreo E-commerce</p>
  <h2 class="intro-lead">New generation websites by <b>new generation designers.</b><br>For new generation entrepreneurs..</h2>
  <div class="intro-cols">
    <div class="intro-col">
      <svg width="64" height="56" viewBox="0 0 64 56"><rect x="4" y="4" width="56" height="40" rx="2" fill="none" stroke="#f07f1b" stroke-width="3"/><path d="M26 16l-8 8 8 8M38 16l8 8-8 8M34 14l-4 20" stroke="#f07f1b" stroke-width="3" fill="none"/><path d="M18 52h28" stroke="#f07f1b" stroke-width="3"/></svg>
      <h3>Torvista Certified Developer</h3>
      <p>It is a long established fact that a reader will be distracted by the readable content of a page when looking at its layout. The point of using Lorem Ipsum is that it has a more-or-less normal distribution of letters, as opposed to using , making it look like readable English.</p>
    </div>
    <div class="intro-col">
      <svg width="64" height="56" viewBox="0 0 64 56"><path d="M32 10a14 14 0 0 0-8 25v7h16v-7a14 14 0 0 0-8-25z" fill="none" stroke="#f07f1b" stroke-width="3"/><path d="M26 48h12M32 0v5M12 8l4 4M52 8l-4 4M6 24h6M52 24h6" stroke="#f07f1b" stroke-width="3"/></svg>
      <h3>Torvista Certified Solution Provider</h3>
      <p>It is a long established fact that a reader will be distracted by the readable content of a page when looking at its layout. The point of using Lorem Ipsum is that it has a more-or-less normal distribution of letters, as opposed to using , making it look like readable English.</p>
    </div>
  </div>
</section>

<section class="services">
  <h2 class="section-title">What <b>We Do</b></h2>
  <p class="section-sub">Simply dummy text of the printing and typesetting industry.</p>
  <div class="service-cards">
    <article class="service-card">
      <div class="service-icon" style="background:#4eb6b0"><svg width="40" height="34"><rect x="2" y="2" width="36" height="24" rx="2" fill="#fff"/><path d="M16 9l-4 5 4 5M24 9l4 5-4 5" stroke="#e64c3c" stroke-width="2" fill="none"/><path d="M14 32h12" stroke="#fff" stroke-width="3"/></svg></div>
      <h3>Web Development</h3>
      <p>It is a long established fact that a reader will be distracted the readable content.</p>
      <a class="btn-grey" href="#">Read More</a>
    </article>
    <article class="service-card">
      <div class="service-icon" style="background:#f5a623"><svg width="40" height="40"><path d="M8 22a12 12 0 0 1 24 0" stroke="#fff" stroke-width="3" fill="none"/><rect x="4" y="20" width="7" height="12" rx="2" fill="#fff"/><rect x="29" y="20" width="7" height="12" rx="2" fill="#fff"/><path d="M32 32q0 5-8 5" stroke="#fff" stroke-width="2" fill="none"/></svg></div>
      <h3>Web Support</h3>
      <p>It is a long established fact that a reader will be distracted the readable content.</p>
      <a class="btn-grey" href="#">Read More</a>
    </article>
    <article class="service-card">
      <div class="service-icon" style="background:#4eb6b0"><svg width="40" height="40"><path d="M8 32L26 14M10 10l22 22" stroke="#fff" stroke-width="5" stroke-linecap="round"/><circle cx="28" cy="11" r="6" fill="none" stroke="#fff" stroke-width="3"/></svg></div>
      <h3>Web Maintenance</h3>
      <p>It is a long established fact that a reader will be distracted the readable content.</p>
      <a class="btn-grey" href="#">Read More</a>
    </article>
  </div>
  <p class="services-note">High performance Torvista sites on time and on budget.</p>
  <a class="btn-outline-white" href="#">Contact Us Now!</a>
</section>

<section class="testimonials">
  <h2 class="section-title">Client <b>Testimonials</b></h2>
  <p class="section-sub">What our Customers say About us and Reviews</p>
  <div class="client-photo" role="img" aria-label="Portrait photo of the client in a suit"></div>
  <blockquote class="quote">
    <p>" Lorem Ipsum is simply dummy text of the printing and typesetting industry. Lorem Ipsum has been the industry's standard dummy text ever since the 1500s, when an unknown printer took a galley of type and scrambled it to make a type specimen book. It has survived not only five centuries "</p>
    <cite>Harold Brenwick, <span>USA</span></cite>
  </blockquote>
</section>

<section class="portfolio">
  <h2 class="section-title">Our <b>Portfolio</b></h2>
  <p class="section-sub">Simply dummy text of the printing and typesetting industry.</p>
  <a class="portfolio-arrow prev" href="#"><svg width="22" height="60"><path d="M20 2 3 30l17 28" stroke="#555" stroke-width="1.5" fill="none"/></svg></a>
  <div class="project-list">
    <article class="project"><div class="project-shot" role="img" aria-label="Screenshot of a medical clinic website" style="background:linear-gradient(180deg,#3a7fc1 0%,#9cc3e2 45%,#e9eef3 100%)"></div><p>Our project name 01</p></article>
    <article class="project"><div class="project-shot" role="img" aria-label="Screenshot of a creative design agency website" style="background:linear-gradient(180deg,#f2f2f2 0%,#e3e3e3 50%,#d84a4a 80%,#f2f2f2 100%)"></div><p>Our project name 02</p></article>
    <article class="project"><div class="project-shot" role="img" aria-label="Screenshot of a wedding photography website" style="background:linear-gradient(180deg,#7fc0e8 0%,#cfe6f4 45%,#f7f7f7 100%)"></div><p>Our project name 03</p></article>
    <article class="project"><div class="project-shot" role="img" aria-label="Screenshot of a travel website with tropical beach" style="background:linear-gradient(180deg,#3f8fbf 0%,#5aa868 25%,#eef3f6 55%,#ffffff 100%)"></div><p>Our project name 04</p></article>
  </div>
  <a class="portfolio-arrow next" href="#"><svg width="22" height="60"><path d="M2 2l17 28L2 58" stroke="#555" stroke-width="1.5" fill="none"/></svg></a>
  <a class="btn-outline-orange" href="#">View More</a>
</section>

<div class="tech-strip bottom">
  <span>MarkSix</span><span><i></i>Torvista</span><span>Ferrite</span><span>QRX</span><span>NCB</span><span>DataVane</span>
</div>

<footer class="site-footer">
  <div class="footer-col" style="left:132px">
    <h4>Quick Links</h4>
    <ul class="footer-links"><li>- Home</li><li>- About Us</li><li>- Torvista</li><li>- Our Portfolio</li><li>- Contact Us</li></ul>
  </div>
  <div class="footer-col" style="left:286px">
    <h4>Sign Up Newsletter</h4>
    <p>Simply dummy text of the printing and<br>typesetting industry.</p>
    <div class="news-input"><svg width="14" height="10"><rect width="14" height="10" fill="#ccc"/><path d="M0 0l7 6 7-6" stroke="#444" fill="none"/></svg>Email Address</div>
    <div class="news-btn">Submit</div>
  </div>
  <div class="footer-col" style="left:564px">
    <h4>Contact Us</h4>
    <p>Suite 42, Level 3, 8 Wattlebrook Lane,<br>Fernvale Heights VIC 3999</p>
    <p style="margin-top:10px">Phone:<br>1300 648 907</p>
    <p style="margin-top:10px">Email:<br>info@kavreo.example</p>
  </div>
  <div class="footer-map" role="img" aria-label="Street map with a location pin at the office address"></div>
  <a class="map-link" href="#">View Plotway Map</a>
</footer>
<div class="copyright">Copyright © 2016 - <em>Kavreo E-commerce</em>. All Rights Reserved</div>

</body>
</html>
```